Northfield Builders Guild Business card

We are looking for a new business card design with photo included.
Our business is a nonprofit construction contractor membership organization. We offer business education, assist with business setup and licensing, provide safety training, and provide a member directory.
URL: www.builderslinkguild.org
Color code:
CMYK: 0 cyan, 42 magenta, 100 yellow, 0 black for Print.
Hexidecimal: #FF9900
RGB: R 255; G 153; B 0

```html
<!DOCTYPE html>
<html lang="en">
<head>
<meta charset="utf-8">
<title>Northfield Builders Guild – Business Card</title>
<link href="https://fonts.googleapis.com/css2?family=Jost:wght@400;500;700&display=swap" rel="stylesheet">
<style>
  :root {
    --backdrop: #8b8b8b;
    --paper: #ffffff;
    --ink: #353334;
    --ink-soft: #4a4849;
    --brand-orange: #ff9900;
    --back-card: #353334;
    --back-mark: #8e8c8d;
  }
  * { box-sizing: border-box; margin: 0; padding: 0; }
  html, body {
    width: 1200px; height: 1200px; overflow: hidden;
    background: var(--backdrop);
    font-family: "Jost", "Helvetica Neue", Arial, sans-serif;
  }
  .canvas { position: relative; width: 1200px; height: 1200px; }

  .card {
    position: absolute; left: 262px; width: 686px; height: 392px;
  }
  .card--front { top: 165px; background: var(--paper); color: var(--ink); }
  .card--back { top: 653px; background: var(--back-card); }

  .wordmark {
    position: absolute; left: 0; right: 0;
    text-align: center; font-weight: 700; text-transform: uppercase;
    letter-spacing: 1px; font-size: 34px; line-height: 1;
  }
  .card--front .wordmark { top: 112px; color: var(--ink); }
  .card--back .wordmark { top: 178px; color: var(--back-mark); }

  .divider { position: absolute; top: 250px; height: 3px; }
  .divider--accent { left: 39px; width: 205px; background: var(--brand-orange); }
  .divider--main { left: 246px; width: 394px; background: var(--ink); }

  .identity { position: absolute; left: 41px; top: 275px; }
  .identity__name {
    font-weight: 700; font-size: 25px; line-height: 1.1;
    text-transform: uppercase; letter-spacing: 0.3px; color: var(--ink);
  }
  .identity__role { font-size: 16.5px; color: var(--brand-orange); line-height: 1.25; }
  .identity__address { margin-top: 5px; font-size: 16.5px; line-height: 1.2; color: var(--ink-soft); }

  .contacts {
    position: absolute; right: 40px; top: 282px;
    list-style: none; font-size: 16px; line-height: 19.5px; color: var(--ink-soft);
  }
  .contacts li { display: flex; justify-content: flex-end; align-items: center; gap: 9px; }
  .contacts svg { width: 13px; height: 13px; flex: none; fill: var(--brand-orange); }
</style>
</head>
<body>
<div class="canvas">
  <section class="card card--front">
    <div class="wordmark">Northfield Builders Guild</div>

    <div class="divider divider--accent"></div>
    <div class="divider divider--main"></div>

    <div class="identity">
      <div class="identity__name">Daniel Hayes</div>
      <div class="identity__role">President</div>
      <div class="identity__address">4200 Ridgeway Ave.,<br>Suite #210, Northfield, OR 97402</div>
    </div>

    <ul class="contacts">
      <li>(555) 410-2287
        <svg viewBox="0 0 16 16"><path d="M3.5 1 6 1.5 7 5 5.3 6.3c.9 1.9 2.4 3.5 4.4 4.4L11 9l3.5 1 .5 2.5-2 2C7 14 2 9 1.5 3z"/></svg>
      </li>
      <li>555.318.0642
        <svg viewBox="0 0 16 16"><path d="M4 0h8a1 1 0 0 1 1 1v14a1 1 0 0 1-1 1H4a1 1 0 0 1-1-1V1a1 1 0 0 1 1-1zm1 2v11h6V2z"/></svg>
      </li>
      <li>help@nbguild.org
        <svg viewBox="0 0 16 16"><path d="M1 4h14v9H1zM2 5l6 4 6-4v-.2H2z" fill-rule="evenodd"/></svg>
      </li>
      <li>www.builderslinkguild.org
        <svg viewBox="0 0 16 16"><circle cx="8" cy="8" r="7"/><path d="M4 5c2 0 2 2 4 2s1 3 3 3" stroke="#fff" stroke-width="1.4" fill="none"/></svg>
      </li>
    </ul>
  </section>

  <section class="card card--back">
    <div class="wordmark">Northfield Builders Guild</div>
  </section>
</div>
</body>
</html>
```